Business card design

I need my logo on this card, things I need the card to have on it
licensed and insured.
owner operators Milo & Trent Halvorsen
my phone number 5083716254
Disaster Recovery, Storm Damage Restoration, Proactive Disaster Plan Management, Roof Repair/Restoration Structural Repair and Reconstruction, Emergency Boarding and Tarping Service, Perimeter Fencing, Emergency Tree Removal,

```html
<!DOCTYPE html>
<html lang="en">
<head>
<meta charset="utf-8">
<title>Halvorsen's Construction L.L.C — Business Card</title>
<link rel="stylesheet" href="https://fonts.googleapis.com/css2?family=Questrial&family=Exo+2:wght@400;500&display=swap">
<style>
  :root {
    --backdrop: #d4d5d7;
    --card-dark: #151515;
    --card-light: #ffffff;
    --brand-blue: #3b8fd4;
    --text-light: #f2f2f2;
    --text-grey: #4d4d4f;
    --text-mid: #5e5e60;
  }
  * { margin: 0; padding: 0; box-sizing: border-box; }
  html, body { width: 900px; height: 1200px; overflow: hidden; }
  body { background: var(--backdrop); position: relative; font-family: "Questrial", sans-serif; }

  .card { position: absolute; left: 133px; width: 633px; height: 364px; }
  .card--front { top: 210px; background: var(--card-dark); }
  .card--back { top: 624px; background: var(--card-light); }

  .brand-name {
    position: absolute;
    display: flex; align-items: center; gap: 10px;
    color: var(--brand-blue);
    font-family: "Questrial", sans-serif;
    font-weight: 400;
    font-size: 25px;
    line-height: 1.15;
    text-align: center;
  }
  .brand-name__mark { width: 14px; height: 14px; background: var(--brand-blue); flex: none; }
  .card--front .brand-name { left: 40px; top: 150px; width: 260px; justify-content: center; }
  .card--back .brand-name { left: 390px; top: 60px; width: 218px; justify-content: center; }

  .services { position: absolute; left: 330px; top: 44px; }
  .services__title {
    color: var(--brand-blue);
    font-family: "Questrial", sans-serif;
    font-size: 17px; letter-spacing: 0.3px;
    margin-bottom: 10px;
  }
  .services__list { list-style: none; font-family: "Exo 2", sans-serif; font-size: 14px; color: var(--text-light); }
  .services__item { position: relative; padding-left: 20px; line-height: 22.5px; margin-bottom: 7.5px; letter-spacing: 0.2px; }
  .services__item::before {
    content: ""; position: absolute; left: 1px; top: 6px;
    width: 10px; height: 10px; background: var(--brand-blue);
  }

  .licence {
    position: absolute; left: 395px; top: 163px; width: 210px;
    text-align: center; color: var(--text-grey);
    font-size: 15px; letter-spacing: 1.3px;
  }

  .contact { position: absolute; left: 29px; top: 212px; }
  .contact__names { color: var(--brand-blue); font-size: 20px; letter-spacing: 0.3px; }
  .contact__role { color: var(--text-mid); font-size: 15px; letter-spacing: 0.8px; margin-top: 4px; margin-left: 2px; }
  .contact__lines { list-style: none; margin-top: 12px; }
  .contact__line { display: flex; align-items: center; gap: 7px; color: var(--text-grey); font-size: 15px; height: 23px; }
  .contact__line--phone { font-size: 16px; letter-spacing: 1.4px; }
  .contact__icon { width: 15px; height: 15px; flex: none; }
</style>
</head>
<body>

  <section class="card card--front">
    <div class="brand-name"><span class="brand-name__mark"></span><span>Halvorsen's<br>Construction L.L.C</span></div>

    <div class="services">
      <h2 class="services__title">OUR SERVICES:</h2>
      <ul class="services__list">
        <li class="services__item">Disaster Recovery</li>
        <li class="services__item">Storm Damage Restoration</li>
        <li class="services__item">Proactive Disaster Plan Management</li>
        <li class="services__item">Roof Repair/Restoration Structural<br>Repair and Reconstruction</li>
        <li class="services__item">Emergency Boarding and<br>Tarping Service</li>
        <li class="services__item">Perimeter Fencing</li>
        <li class="services__item">Emergency Tree Removal</li>
      </ul>
    </div>
  </section>

  <section class="card card--back">
    <div class="brand-name"><span class="brand-name__mark"></span><span>Halvorsen's<br>Construction L.L.C</span></div>
    <p class="licence">LICENSED AND INSURED</p>

    <div class="contact">
      <h1 class="contact__names">Milo &amp; Trent Halvorsen</h1>
      <p class="contact__role">Owner Operator</p>
      <ul class="contact__lines">
        <li class="contact__line contact__line--phone">
          <svg class="contact__icon" viewBox="0 0 24 24" aria-hidden="true"><path fill="#3b8fd4" d="M6.6 10.8a15.1 15.1 0 0 0 6.6 6.6l2.2-2.2a1 1 0 0 1 1-.25 11.4 11.4 0 0 0 3.6.57 1 1 0 0 1 1 1V20a1 1 0 0 1-1 1A17 17 0 0 1 3 4a1 1 0 0 1 1-1h3.5a1 1 0 0 1 1 1c0 1.25.2 2.45.57 3.57a1 1 0 0 1-.25 1z"/></svg>
          5083716254
        </li>
        <li class="contact__line">
          <svg class="contact__icon" viewBox="0 0 24 24" aria-hidden="true"><rect x="2" y="5" width="20" height="14" fill="#3b8fd4"/><path d="M2 5l10 8 10-8" fill="none" stroke="#fff" stroke-width="1.6"/></svg>
          info@halvorsenconstructionllc.com
        </li>
        <li class="contact__line">
          <svg class="contact__icon" viewBox="0 0 24 24" aria-hidden="true"><g fill="none" stroke="#3b8fd4" stroke-width="1.6"><circle cx="12" cy="12" r="9.5"/><ellipse cx="12" cy="12" rx="4" ry="9.5"/><path d="M2.5 12h19M4 7h16M4 17h16"/></g></svg>
          halvorsenconstructionllc.com
        </li>
      </ul>
    </div>
  </section>

</body>
</html>
```